Specialised investor in e-mobility and energy wants business card design

We need a business card design that fits our existing corporate design. <The look and feel must be 'sharp'/'clean', dynamic, communicate momentum, professionalism etc (as one would imagine from a firm in the financial sector). We like the idea of a reverse-side of the card that includes the logo, and the name and contact details on the other. We expect the deliverable to be whatever format might be required to be able to get cards printed directly by a service such as kelmo press. Our website is www.zub.capital

```html
<!DOCTYPE html>
<html lang="en">
<head>
<meta charset="utf-8">
<title>ZUB Capital – Business Card</title>
<link href="https://fonts.googleapis.com/css2?family=Poppins:wght@400;500;600&display=swap" rel="stylesheet">
<style>
  :root {
    --bg: #e9ebe9;
    --green-dark: #154d1a;
    --green-light: #6db33f;
    --white: #ffffff;
    --card-w: 760px;
    --card-h: 440px;
  }
  * { margin: 0; padding: 0; box-sizing: border-box; }
  html, body {
    width: 1200px; height: 1200px; overflow: hidden;
    background: var(--bg);
    font-family: "Poppins", sans-serif;
  }
  .canvas {
    width: 1200px; height: 1200px;
    display: flex; flex-direction: column;
    align-items: center; justify-content: center; gap: 70px;
  }
  .card {
    position: relative;
    width: var(--card-w); height: var(--card-h);
    border-radius: 38px; overflow: hidden;
    background: var(--green-dark);
    box-shadow: 0 10px 30px rgba(0,0,0,.18);
  }
  .card-shape { position: absolute; inset: 0; }
  .brand-name {
    position: absolute;
    font-weight: 500; letter-spacing: 1px; white-space: nowrap;
  }
  .card-front .brand-name {
    left: 70px; top: 185px; font-size: 52px; color: var(--green-dark);
  }
  .card-back .brand-name {
    left: 0; right: 0; top: 175px; text-align: center;
    font-size: 74px; color: var(--white);
  }
  .contact {
    position: absolute; left: 520px; top: 108px; color: var(--white);
  }
  .contact .person-name {
    font-size: 30px; font-weight: 600; color: var(--green-light); line-height: 1;
  }
  .contact .person-role {
    font-size: 22px; margin: 4px 0 22px 14px; line-height: 1;
  }
  .contact-list { list-style: none; margin-left: 30px; }
  .contact-list li {
    display: flex; align-items: center; gap: 12px;
    font-size: 19px; line-height: 1.55;
  }
  .contact-list svg { width: 20px; height: 20px; flex: none; }
</style>
</head>
<body>
<main class="canvas">

  <section class="card card-front" aria-label="Business card front">
    <svg class="card-shape" viewBox="0 0 760 440" preserveAspectRatio="none">
      <path d="M0 0 H300 C470 60 565 250 470 440 H0 Z" fill="var(--white)"/>
      <path d="M312 4 C490 70 590 250 492 440 L474 440 C565 250 478 66 312 4 Z" fill="var(--green-light)"/>
    </svg>
    <div class="brand-name">ZUB Capital</div>
    <div class="contact">
      <div class="person-name">FULL NAME</div>
      <div class="person-role">POSITION</div>
      <ul class="contact-list">
        <li>
          <svg viewBox="0 0 24 24"><path fill="var(--green-light)" d="M6.6 10.8a15.1 15.1 0 0 0 6.6 6.6l2.2-2.2c.3-.3.7-.4 1-.2 1.1.4 2.3.6 3.6.6.6 0 1 .4 1 1V20c0 .6-.4 1-1 1A17 17 0 0 1 3 4c0-.6.4-1 1-1h3.5c.6 0 1 .4 1 1 0 1.3.2 2.5.6 3.6.1.3 0 .7-.2 1z"/></svg>
          +41 70418 5527
        </li>
        <li>
          <svg viewBox="0 0 24 24"><rect x="2" y="5" width="20" height="14" rx="1" fill="var(--green-light)"/><path d="M2 6 L12 13 L22 6" stroke="var(--green-dark)" stroke-width="1.6" fill="none"/></svg>
          john@zub.capital
        </li>
        <li>
          <svg viewBox="0 0 24 24" fill="none" stroke="var(--green-light)" stroke-width="1.6"><circle cx="12" cy="12" r="9.5"/><ellipse cx="12" cy="12" rx="4" ry="9.5"/><path d="M2.5 12h19M4 7h16M4 17h16"/></svg>
          www.zub.capital
        </li>
      </ul>
    </div>
  </section>

  <section class="card card-back" aria-label="Business card back">
    <div class="brand-name">ZUB Capital</div>
  </section>

</main>
</body>
</html>
```